A private security company called "Tavron Security Services Ltd"

Hello everybody,

We need a web page for a company based in NZ. It is mainly an informative website so it would be wonderful if the designer puts their absolute best into making it a website that I would really appreciate. The website needs to show professionalism and also needs to make our web surfers find the information they need in a click. the company's colour is black and silver, and if those two colours could be integrated into the website it would be absolutely lovely. Please do contact me for any information.

Sincerely,
Dorian Vaskel

Industry/Entity Type

Security

```html
<!DOCTYPE html>
<html lang="en">
<head>
<meta charset="utf-8">
<title>Tavron Security Services Ltd</title>
<link href="https://fonts.googleapis.com/css2?family=Open+Sans:wght@300;400;600;700&display=swap" rel="stylesheet">
<style>
:root{
  --black:#0c0c0c;
  --header-top:#3a3a3a;
  --footer:#1b1b1b;
  --white:#ffffff;
  --silver:#d9d9d9;
  --text-dark:#1c1c1c;
  --text-body:#2e2e2e;
  --text-muted:#9a9a9a;
  --band:#f3f3f3;
  --hero-a:#e4e7ea;
  --hero-b:#b9c2cb;
}
*{margin:0;padding:0;box-sizing:border-box}
html,body{width:829px;height:1200px;overflow:hidden;background:var(--white)}
body{font-family:"Open Sans",Arial,sans-serif;position:relative;color:var(--text-dark)}
.abs{position:absolute}

/* header */
.site-header{left:0;top:0;width:829px;height:105px;background:linear-gradient(var(--header-top),var(--black) 60%)}
.brand{left:76px;top:50px;color:var(--white);font-weight:600;text-transform:uppercase}
.brand-name{font-size:19px;letter-spacing:3px;line-height:20px}
.brand-sub{font-size:7.4px;letter-spacing:.6px;line-height:10px}
.call{right:76px;top:14px;color:var(--white);font-size:28px;font-weight:300;white-space:nowrap}
.call b{font-weight:600}
.main-nav{right:72px;top:66px;display:flex;gap:0}
.main-nav a{color:var(--white);font-size:10px;text-decoration:none;padding:4px 10.5px;line-height:14px}
.main-nav a.active{background:var(--white);color:var(--text-dark);border-radius:2px;font-weight:600;padding:4px 12px}

/* hero */
.hero{left:0;top:105px;width:829px;height:322px;background:linear-gradient(100deg,var(--hero-a),var(--silver) 50%,var(--hero-b))}
.hero-curve{left:0;top:398px}
.hero-title{left:70px;top:163px;font-size:38px;font-weight:300;letter-spacing:-1.5px;color:var(--text-dark);line-height:48px}
.hero-title b{font-weight:700}
.hero-text{left:77px;top:224px;width:380px;font-size:11.3px;line-height:15.2px;color:var(--text-body)}
.btn-light{left:77px;top:326px;width:91px;height:28px;background:linear-gradient(#f2f2f2,#c9c9c9);border-radius:2px;font-size:9.5px;font-weight:600;text-align:center;line-height:28px;color:var(--text-dark)}
.hero-visual{left:512px;top:140px;width:244px;height:215px;border-radius:6px;background:radial-gradient(ellipse at 55% 45%,#e9e5dc,#c9c6bd 55%,rgba(185,194,203,0) 75%)}
.dots{left:401px;top:413px;display:flex;gap:3px}
.dots span{width:6px;height:6px;border-radius:50%;background:var(--text-dark)}

/* services */
.section-title{left:0;width:829px;text-align:center;font-size:20px;font-weight:600;color:var(--text-dark);letter-spacing:-.3px}
.services-title{top:447px}
.divider{left:76px;top:486px;width:677px;height:4px;background:radial-gradient(ellipse at center,rgba(0,0,0,.06),rgba(0,0,0,0) 70%)}
.service{top:512px;width:156px}
.service h3{font-size:11.2px;font-weight:600;letter-spacing:-.1px;height:25px;white-space:nowrap}
.service .photo{width:156px;height:106px}
.service p{margin-top:12px;font-size:8.6px;line-height:15px;color:var(--text-muted);font-weight:300}
.photo-control{background:linear-gradient(135deg,#6f8aa3,#2f3d4e 60%,#c9783e)}
.photo-patrol{background:linear-gradient(#8ea5a8,#9a9a8d 45%,#555 100%)}
.photo-camera{background:linear-gradient(#5d9bd8,#a9cde9 70%,#6a7b8d)}
.photo-officer{background:linear-gradient(90deg,#4a6d9c,#223754 55%,#c97a9a)}

/* about */
.about-band{left:0;top:740px;width:829px;height:245px;background:var(--band)}
.about-photo{left:76px;top:767px;width:330px;height:177px;background:radial-gradient(ellipse at 70% 40%,#e6962c,#9a4a0e 45%,#120804 85%)}
.about-label{left:104px;top:850px;color:var(--white);font-size:27px;font-weight:600;letter-spacing:.3px}
.about-title{left:440px;top:760px;font-size:21px;font-weight:600;color:var(--text-dark)}
.about-text{left:440px;width:305px;font-size:8.6px;line-height:13.2px;color:var(--text-muted)}
.btn-dark{left:440px;top:921px;width:77px;height:23px;background:linear-gradient(#3a3a3a,#0f0f0f);color:var(--white);font-size:9.5px;text-align:center;line-height:23px;border-radius:2px}

/* footer */
.site-footer{left:0;top:985px;width:829px;height:215px;background:var(--footer)}
.foot-h{top:1014px;color:var(--white);font-size:10.5px;font-weight:600}
.foot-list{list-style:none;color:#d6d6d6;font-size:8.8px}
.foot-list li.current{color:var(--white);font-weight:600}
.testimonial-box{left:380px;top:1043px;width:161px;height:66px;background:var(--white);border-radius:2px;padding:5px 8px;font-size:8.2px;line-height:14px;color:#b4b4b4;text-align:center;font-weight:300}
.field{background:var(--white);border-radius:2px;font-size:8.4px;color:#8a8a8a;padding:4px 6px}
.send{left:677px;top:1124px;width:61px;height:23px;background:linear-gradient(#f4f4f4,#c7c7c7);border-radius:2px;font-size:10px;font-weight:600;text-align:center;line-height:23px;color:var(--text-dark)}
.copyright{left:0;top:1175px;width:829px;text-align:center;color:#e6e6e6;font-size:8px}
</style>
</head>
<body>

<header class="abs site-header">
  <div class="abs brand">
    <div class="brand-name">Tavron</div>
    <div class="brand-sub">Security Services Ltd.</div>
  </div>
  <div class="abs call"><b>Call:</b> 021 555 0148</div>
  <nav class="abs main-nav">
    <a class="active" href="#">Home</a>
    <a href="#">About Us</a>
    <a href="#">Security Services</a>
    <a href="#">Why Us</a>
    <a href="#">Testimonials</a>
    <a href="#">Contct Us</a>
  </nav>
</header>

<section class="abs hero"></section>
<div class="abs hero-visual" role="img" aria-label="Wall-mounted security camera"></div>
<svg class="abs hero-curve" width="829" height="30" viewBox="0 0 829 30"><path d="M0 28 Q414 -14 829 28 L829 30 L0 30 Z" fill="#ffffff"/></svg>
<h1 class="abs hero-title">WE <b>SECURE</b> YOUR LIFE</h1>
<p class="abs hero-text">Lorem ipsum dolor sit amet, consectetur adipisicing elit, sed&nbsp; eiusmod tempor incididunt ut labore et dolore magna aliqua ut enim ad minim veniam, quis nostrud exercitation ullamco laborisnisi ut aliquip ex ea commodo consequat. Duis aute irure dolor in reprehenderit in voluptate velit esse cillum dolore eu fugiat nulla pariatur. Excepteur sint occaecat cupidatat non proident, sunt in</p>
<div class="abs btn-light">Read More</div>
<div class="abs dots"><span></span><span></span><span></span></div>

<h2 class="abs section-title services-title">OUR SERVICES</h2>
<div class="abs divider"></div>

<article class="abs service" style="left:76px">
  <h3>GUARD SERVICES</h3>
  <div class="photo photo-control" role="img" aria-label="Guard on the phone in a monitoring room"></div>
  <p>Lorem ipsum dolor consectetur adiicing sed eiusmod tempor incidiunt&nbsp; labore dolore magna aliqua ut enim ad minim veniam nostrud exercitation.</p>
</article>
<article class="abs service" style="left:250px">
  <h3>SECURITY PATROLS</h3>
  <div class="photo photo-patrol" role="img" aria-label="Patrol officer with dog beside patrol car"></div>
  <p>Lorem ipsum dolor consectetur adiicing sed eiusmod tempor incidiunt&nbsp; labore dolore magna aliqua ut enim ad minim veniam nostrud exercitation.</p>
</article>
<article class="abs service" style="left:424px">
  <h3>FIXED CAMRA SYSTEMS</h3>
  <div class="photo photo-camera" role="img" aria-label="Fixed camera overlooking a city skyline"></div>
  <p>Lorem ipsum dolor consectetur adiicing sed eiusmod tempor incidiunt&nbsp; labore dolore magna aliqua ut enim ad minim veniam nostrud exercitation.</p>
</article>
<article class="abs service" style="left:597px">
  <h3>ARMED SECURITY OFFICERS</h3>
  <div class="photo photo-officer" role="img" aria-label="Officer duty belt with holster"></div>
  <p>Lorem ipsum dolor consectetur adiicing sed eiusmod tempor incidiunt&nbsp; labore dolore magna aliqua ut enim ad minim veniam nostrud exercitation.</p>
</article>

<section class="abs about-band"></section>
<div class="abs about-photo" role="img" aria-label="Security staff in front of a crowd"></div>
<div class="abs about-label">SECURITY</div>
<h2 class="abs about-title">ABOUT US</h2>
<p class="abs about-text" style="top:795px">Lorem ipsum dolor sit amet consectetur adipisicing elit sed eiusmod tempor incididunt ut labore et dolore magna aliqua ut enim ad minim veniam quis nostrud exercitation ullamco laboris nisi aliquip ex commodo consequat sunt in culpa qui officia deserunt mollit anim id est laborum</p>
<p class="abs about-text" style="top:861px">Lorem ipsum dolor sit amet, consectetur adipisicing elit, sed do eiusmod tempor incididunt ut labore et dolore magna aliqua. Ut enim ad minim veniam, quis nostrud exercitation ullamco</p>
<div class="abs btn-dark">Read More</div>

<footer class="abs site-footer"></footer>
<h4 class="abs foot-h" style="left:91px">SITE MAP</h4>
<ul class="abs foot-list" style="left:91px;top:1039px;line-height:13.8px">
  <li class="current">Home</li><li>About Us</li><li>Security Services</li><li>Why Us</li><li>Testimonials</li><li>Contct Us</li>
</ul>
<h4 class="abs foot-h" style="left:217px">LINKS</h4>
<ul class="abs foot-list" style="left:217px;top:1039px;line-height:15.2px">
  <li>Lorem ipsum dolor sit</li><li>Ame cnsectetur adipisicing</li><li>Elit sed&nbsp; eiusmod tempor</li><li>Incididunt ut labore et</li><li>Dolore magna</li>
</ul>
<h4 class="abs foot-h" style="left:379px">TESTIMONIALS</h4>
<div class="abs testimonial-box">Lorem ipsum dolor sit ame cnsecte-tur adipisicing elit&nbsp; eiusmod tempor incididunt ut labore et dolore magna aliqua ut enim ad minim. veniam,</div>
<h4 class="abs foot-h" style="left:591px;top:1012px">QUICK CONTACT</h4>
<div class="abs field" style="left:591px;top:1043px;width:147px;height:20px">Email Adderss</div>
<div class="abs field" style="left:591px;top:1068px;width:147px;height:45px">Massage</div>
<div class="abs send">SEND</div>
<p class="abs copyright">Copy rigthe 2014 ©. Tavron Security Center. All rights reserved</p>

</body>
</html>
```